Residential Mortgage Leader needs Wordpress Design

Looking for a home page website design for a client. We develop using the WordPress platform and would prefer the design be at least loosely based on an existing WordPress template. Attached files have many notes from our creative brief with client. The site must be responsive. Approved, basic wireframe attached. There is room for interpretation.

Existing web site: http://www.marisolkettering.example/

The Marisol Kettering Team relies on strong systems to deliver an on-time, done-right, friendly experience. Marisol offers mortgages and refinancing services throughout the United States. She is a successful Brookvale Funding agent who strives to be an active part of her community. She would like to focus the site on her team, rather than just her.

Difference makers...
When you work with the Marisol Kettering team you get a high level of expertise and a friendly experience.

She has amazing credentials. Marisol is widely recognized as a top producer for her company, and has earned a number of awards and honors for her customer service.

Marisol's team is very engaged and enjoys sharing social comments or photos from their community.

Imagery:
* Friendly, warm imagery, preferably of her team or an image to represent her team
* Clean and crisp
* Professional / Experts in mortgage and refinance
* Clean / Good use of white space
Updates

When possible, please use imagery from the DFW area. The client mentioned they would prefer not to see stock images. Thanks.

Amend that- creative use of stock images, however, is fine. A few designs have used stock imagery, but in a well-considered manner.

We added some photos and graphics that are local. We are Dallas / Ft. Worth, Plano, Frisco, Texas. We also added some examples of photos to use for the "In the Community" area. Stock photos of business folks just doesn't fit there. Thanks!

Target Market(s)

They service a lot of builders, but also work with homeowners. Their typical client is usually a woman searching for mortgage services online. She typically has a family and may refer her husband to Marisol's team. Keep in mind, however, they also see a number of other scenarios. Most of their clients are middle to high-end borrowers.

Industry/Entity Type

It Company

Requirements
Must have
• Design should be developed using program such as Photoshop or Fireworks or Illustrator as last preference. Ideally, the design would be based on an existing responsive WordPress theme, which we would customize. You must include the name of the target theme. The footer should include lots of space for disclaimers and legal language. Site navigation should include these choices: "Home, About, Builders, Mortgage Info, Approval, Blog, Contact"
Nice to have
• Blog, social media and photos area. Use of the already approved style prototype with colors and fonts (Lato- a Google font, Times New Roman and Cookie-a decorative Google font). However, we are open to interpretation.
Should not have
• Hard to read fonts or a lack of white space.

```html
<!DOCTYPE html>
<html lang="en">
<head>
<meta charset="utf-8">
<title>Brookvale Funding – Marisol Kettering Team</title>
<link href="https://fonts.googleapis.com/css2?family=Lato:wght@300;400;700&family=Roboto:wght@400&display=swap" rel="stylesheet">
<style>
:root{
  --red:#c7301c;
  --ink:#333;
  --body:#555;
  --meta:#888;
  --rule:#ddd;
  --footer:#353535;
  --footer-base:#2c2c2c;
  --footer-text:#d8d8d8;
  --white:#fff;
}
*{margin:0;padding:0;box-sizing:border-box}
html,body{width:799px;height:1200px;overflow:hidden;background:var(--white)}
body{position:relative;font-family:'Lato',sans-serif;color:var(--ink)}
.abs{position:absolute}

.brand{left:78px;top:10px}
.brand-mark{width:30px;height:22px;border-radius:50%;background:var(--red);margin-left:32px;margin-bottom:3px}
.brand-name{font-size:17px;font-weight:700;color:var(--red);line-height:1}
.brand-sub{font-size:7.5px;color:var(--ink);margin-top:3px}

.social-top{left:632px;top:30px;display:flex;gap:7px}
.social-top span{width:17px;height:17px;border-radius:2px;display:block}

.main-nav{left:0;top:74px;width:799px;height:34px;background:var(--red)}
.main-nav ul{list-style:none;position:absolute;left:79px;top:0;display:flex;height:34px}
.main-nav li{color:var(--white);font-size:10px;font-weight:400;line-height:34px;padding:0 19px;border-right:1px solid rgba(255,255,255,.25);height:34px}
.main-nav li:last-child{border-right:none}
.main-nav li.active{background:#3b3b3b;padding:0 18px}
.nav-search{position:absolute;left:688px;top:0;width:33px;height:34px;background:#3b3b3b}

.hero{left:0;top:108px;width:799px;height:308px;
  background:
    radial-gradient(ellipse 140px 150px at 560px 210px,rgba(232,236,242,.95),rgba(232,236,242,0) 100%),
    radial-gradient(ellipse 110px 140px at 455px 230px,rgba(150,170,200,.9),rgba(150,170,200,0) 100%),
    radial-gradient(ellipse 60px 50px at 440px 90px,rgba(150,105,70,.9),rgba(150,105,70,0) 100%),
    radial-gradient(ellipse 180px 120px at 250px 110px,rgba(150,95,75,.75),rgba(150,95,75,0) 100%),
    radial-gradient(ellipse 120px 80px at 280px 40px,rgba(240,238,232,.8),rgba(240,238,232,0) 100%),
    linear-gradient(90deg,#8c7d4e 0%,#b7a77c 15%,#c9b9a0 35%,#d4cdc2 55%,#cfd2d4 75%,#a5aa88 92%,#7c8460 100%)}

.cred-row{left:79px;top:325px;width:643px;height:120px;display:flex;background:var(--white);border:1px solid var(--rule)}
.cred{padding:10px 13px 0;height:100%}
.cred h3{font-size:14.5px;font-weight:400;margin-bottom:7px}
.cred p{font-size:7.3px;line-height:14.8px;font-weight:400;color:var(--body)}
.cred-main{width:270px}
.cred-main h3{color:var(--red);margin-bottom:12px}
.cred-main p{max-width:218px}
.cred-center{width:185px;border-left:1px solid var(--rule);text-align:center}
.cred-center.active{border-bottom:2px solid var(--red)}
.cred-side{width:186px;border-left:1px solid var(--rule);text-align:center}
.cred-icon{display:block;margin:0 auto 4px}

.section-head{left:78px;width:666px;border-bottom:1px solid var(--rule)}
.section-head h2{display:inline-block;font-size:14px;font-weight:400;color:var(--red);padding-bottom:4px;border-bottom:1px solid var(--red);margin-bottom:-1px}

.post{width:316px}
.post-img{height:152px}
.post h4{font-size:11.5px;font-weight:400;margin:11px 0 8px -1px}
.post-meta{font-family:'Roboto',sans-serif;font-size:8.3px;color:var(--meta);margin-bottom:9px}
.post-meta b{font-weight:400;color:#555}
.post p{font-size:7.3px;line-height:15px;font-weight:400;color:var(--body)}

.social-item{display:flex;align-items:center;top:816px;width:160px}
.social-item .dot{width:40px;height:40px;border-radius:50%;flex:none;margin-right:7px}
.social-item p{font-size:7.3px;line-height:14.5px;font-weight:400;color:var(--body);width:112px}

.footer{left:0;top:887px;width:799px;height:278px;background:var(--footer)}
.footer-col{top:20px}
.footer-col h3{font-size:14px;font-weight:400;color:var(--white);padding-bottom:8px;border-bottom:1px solid #555;margin-bottom:17px}
.about-text{font-family:'Roboto',sans-serif;font-size:8.4px;line-height:13.4px;color:var(--footer-text);width:150px}
.about-text p+p{margin-top:9px}
.thumbs{display:grid;grid-template-columns:repeat(3,40px);gap:7px}
.thumbs span{height:40px;display:block}
.posts-list{list-style:none;font-family:'Roboto',sans-serif;font-size:8.3px;color:var(--footer-text)}
.posts-list li{padding:9px 0;border-bottom:1px solid #444;line-height:9px}
.contact-card{display:flex}
.contact-photo{width:58px;height:69px;background:linear-gradient(160deg,#6d5a4a,#b69580 60%,#3e3430)}
.contact-name{font-size:9.8px;color:var(--white);line-height:15px;margin:23px 0 0 8px}
.contact-lines{font-size:7.3px;color:var(--footer-text);line-height:14.3px;margin-top:8px}
.footer-base{left:0;top:1165px;width:799px;height:35px;background:var(--footer-base);border-top:1px solid #3d3d3d}
.footer-base p{position:absolute;left:80px;top:12px;font-size:7px;color:var(--footer-text)}
</style>
</head>
<body>

<header>
  <div class="abs brand">
    <div class="brand-mark"></div>
    <div class="brand-name">Brookvale Funding</div>
    <div class="brand-sub">A Harrowgate Company</div>
  </div>
  <div class="abs social-top">
    <span style="background:#1b78b0"></span>
    <span style="background:#3c5a99"></span>
    <span style="background:#2f6fc0"></span>
    <span style="background:#55acee"></span>
  </div>
</header>

<nav class="abs main-nav">
  <ul>
    <li class="active">Home</li>
    <li>About</li>
    <li>Builders</li>
    <li>Mortage Info</li>
    <li>Approval Blog</li>
    <li>Contact Info</li>
  </ul>
  <div class="nav-search">
    <svg width="33" height="34" viewBox="0 0 33 34"><circle cx="15" cy="16" r="3.6" fill="none" stroke="#fff" stroke-width="1.8"/><line x1="17.6" y1="18.6" x2="20.5" y2="21.5" stroke="#fff" stroke-width="2.2" stroke-linecap="round"/></svg>
  </div>
</nav>

<div class="abs hero" role="img" aria-label="Older couple seen from behind, arm in arm, looking at a brick family home"></div>

<section class="abs cred-row">
  <div class="cred cred-main">
    <h3>Our Credentials</h3>
    <p>Lorem Ipsum is simply dummy text of the printing and typesetting industry. Lorem Ipsum has been the industry's standard dummy text ever since the 1500s, when an unknown printer took a galley of type and scrambled.</p>
  </div>
  <div class="cred cred-center active">
    <h3>Awards</h3>
    <svg class="cred-icon" width="26" height="30" viewBox="0 0 30 34"><path d="M10 18 L6 32 L11 29 L13 33 L15 22Z M20 18 L24 32 L19 29 L17 33 L15 22Z" fill="#c7301c"/><circle cx="15" cy="12" r="10" fill="#c7301c"/><circle cx="15" cy="12" r="6" fill="#e0604c"/></svg>
    <p>Lorem Ipsum is simply dummy text of the printing and typesetting industry. Lorem Ipsum has been the industry's.</p>
  </div>
  <div class="cred cred-side">
    <h3>Recognitions</h3>
    <svg class="cred-icon" width="23" height="30" viewBox="0 0 26 34"><rect x="2" y="2" width="22" height="28" rx="3" fill="none" stroke="#c7301c" stroke-width="2"/><circle cx="13" cy="15" r="6.5" fill="none" stroke="#c7301c" stroke-width="1.8"/><path d="M13 10v10M8 15h10M9.5 11.5l7 7M16.5 11.5l-7 7" stroke="#c7301c" stroke-width="1"/></svg>
    <p>Lorem Ipsum is simply dummy text of the printing and typesetting industry. Lorem Ipsum has been the industry's.</p>
  </div>
</section>

<div class="abs section-head" style="top:466px"><h2>Blog</h2></div>

<article class="abs post" style="left:80px;top:521px">
  <div class="post-img" role="img" aria-label="Tired businessman holding his glasses" style="background:radial-gradient(ellipse 90px 70px at 70px 40px,rgba(70,62,58,.9),rgba(70,62,58,0)),radial-gradient(ellipse 110px 80px at 150px 120px,rgba(120,116,110,.9),rgba(120,116,110,0)),linear-gradient(90deg,#6a655e,#a9a49c 40%,#eeeeee 75%,#f6f6f6)"></div>
  <h4>Borrowing</h4>
  <div class="post-meta"><b>Uncategorized</b> - February 10, 2013</div>
  <p>Lorem Ipsum is simply dummy text of the printing and typesetting industry. Lorem Ipsum has been the industry's standard dummy text ever since the 1500s.</p>
</article>
<article class="abs post" style="left:406px;top:521px">
  <div class="post-img" role="img" aria-label="Two businessmen facing each other with megaphones" style="background:radial-gradient(ellipse 40px 60px at 50px 100px,rgba(40,38,36,.9),rgba(40,38,36,0)),radial-gradient(ellipse 40px 60px at 260px 110px,rgba(60,56,52,.85),rgba(60,56,52,0)),radial-gradient(ellipse 50px 25px at 140px 80px,rgba(245,245,242,.9),rgba(245,245,242,0)),radial-gradient(ellipse at 50% 40%,#c9c6c0,#8f8c86 65%,#55524d)"></div>
  <h4>Announcements</h4>
  <div class="post-meta"><b>Uncategorized</b> - January 31, 2013</div>
  <p>Lorem Ipsum is simply dummy text of the printing and typesetting industry. Lorem Ipsum has been the industry's standard dummy text ever since the 1500s.</p>
</article>

<div class="abs section-head" style="top:775px"><h2>Social Media</h2></div>

<div class="abs social-item" style="left:79px"><span class="dot" style="background:#1b84b8"></span><p>Lorem Ipsum is simply dummy text of the printing.</p></div>
<div class="abs social-item" style="left:241px"><span class="dot" style="background:#5868d8"></span><p>Lorem Ipsum is simply dummy text of the printing.</p></div>
<div class="abs social-item" style="left:403px"><span class="dot" style="background:#333"></span><p>Lorem Ipsum is simply dummy text of the printing.</p></div>
<div class="abs social-item" style="left:564px"><span class="dot" style="background:#5868d8"></span><p>Lorem Ipsum is simply dummy text of the printing.</p></div>

<footer class="abs footer">
  <div class="abs footer-col" style="left:79px;width:152px">
    <h3>About Us</h3>
    <div class="about-text">
      <p>Lorem ipsum dolor sit amet, consectetur adipiscing elit. Morbi quis urna eu mi sodales aliquam vitae vitae ligula.<br>Fusce bibendum facilisis lorem vel feugiat. Etiam hendrerit congue nisi, sed cursus lorem pharetra scelerisque. Nulla sollicitudin</p>
      <p>Etiam hendrerit congue nisi, sed cursus lorem pharetra scelerisque. Nulla sollicitudin sagittis pellentesque. Nam a odio vehicula diam porta lacinia</p>
    </div>
  </div>
  <div class="abs footer-col" style="left:245px;width:149px">
    <h3>In the Community</h3>
    <div class="thumbs" role="img" aria-label="Community photos of local streets, landmarks and events" style="margin-left:-2px">
      <span style="background:linear-gradient(#9bc3e6,#e8eef2)"></span>
      <span style="background:linear-gradient(#8fb7de,#d9e4ec)"></span>
      <span style="background:linear-gradient(#b6c9d8,#6f7f8a)"></span>
      <span style="background:linear-gradient(#a4c6e6,#6d6a66)"></span>
      <span style="background:linear-gradient(#9fc2e4,#5f5a55)"></span>
      <span style="background:linear-gradient(#7d8e6e,#6b5d55)"></span>
      <span style="background:linear-gradient(135deg,#b07a5a,#d9d9d9)"></span>
      <span style="background:linear-gradient(135deg,#cf5a4a,#d8dde0)"></span>
      <span style="background:linear-gradient(135deg,#a35d4e,#cfd6d9)"></span>
      <span style="background:linear-gradient(#e0b040,#b6462c)"></span>
      <span style="background:linear-gradient(#d88a3a,#4b7d3a)"></span>
      <span style="background:linear-gradient(#e3e0dc,#c2301f)"></span>
    </div>
  </div>
  <div class="abs footer-col" style="left:409px;width:149px">
    <h3>Recent Posts</h3>
    <ul class="posts-list" style="margin-top:-8px">
      <li>Sed vel tortor tellus. Class aptent</li>
      <li>Hello world!</li>
      <li>PageLoom Theme</li>
      <li>Video Thumb</li>
      <li>The third post</li>
    </ul>
  </div>
  <div class="abs footer-col" style="left:571px;width:151px">
    <h3>Contact Us</h3>
    <div class="contact-card" style="margin-top:-4px">
      <div class="contact-photo" role="img" aria-label="Portrait of the branch manager"></div>
      <div class="contact-name">Marisol Kettering,<br>Branch Manager</div>
    </div>
    <div class="contact-lines">
      Office: 555.214.0386<br>
      Cell: 555.309.7721<br>
      mkettering@brookvalefunding.example<br>
      NMLS: 40218 4820 Elmstead Row, Ste. 110<br>
      Cedar Vale, TX 75000
    </div>
  </div>
</footer>

<div class="abs footer-base"><p>Copyright © Brookvale Funding. All Rights Reserved.</p></div>

</body>
</html>
```